Personal Chef Needs a Good Web Design

Hi everyone!
My name is Leo, I work as a private chef for last 10 years, traveling all around the world and cooking in private megayacht and villas.
I'm about to settle down in my hometown in Europe for a while. And therefore I need a website that will show my story, pics and recipes, nutritional advices and of course offer a Personal and Private Chef services( working for 4-5 families and bringing delicious food to their house).
My clients are extremely rich folks, but usually are down to earth ones.
I believe, the web site should be focused on attention to:
-VIP person's wife( as she is usually responsible for food for family) and be simple.
-to famous people agents and be on high level.

There will be about 10 different menus and 6 different service offers

--UPDATE--
Logo Design:
+My thoughts are- printed structure of the vegetable or fruit on a white font. Like you slice the buffalo tomato, put it in red paint and print it on the edge of the page. See attached files named logo. Can be any nice structured thing, like tomato, lemon, red cabbage etc.
+Classic logos with chef's hat or knives are good too.
+Need to have the space for me to add the name( the fonts can be provided)

Target Market(s)

Private person. 80% Russian clients.

Industry/Entity Type

Cooking

Coding

Coded - Design and coding required

Number of Pages Required

3 page

Requirements
Must have
• Contact form/ Request back call/ Schedule a free consultation
Nice to have
• The client will need to choose straight ahead from the range of services I offer, like:
• -Private Chef( cooking only for the client)
• -Personal Chef( cooking for around 5 clients, bringing the ready to be heated food to their door)
• -Romantic dinner for two
• -Professional Sommelier service
• -Build your kitchen( offering design, equipment and that will fit your requirements)
• -Other( flowers, waiters, barista, equipment rental)
• So this column should go right after the introduction/aboutme part and will lead to separate pages with how-it-works thing for each.

```html
<!DOCTYPE html>
<html lang="en">
<head>
<meta charset="utf-8">
<title>Leo Chef – Private Chef</title>
<link href="https://fonts.googleapis.com/css2?family=Montserrat:wght@300;400;500;600&family=Open+Sans:wght@400;600;700&display=swap" rel="stylesheet">
<style>
:root{
  --accent:#d98f45;
  --accent-dark:#c97f36;
  --ink:#1f1f1f;
  --text:#6b6b6b;
  --muted:#9a9a9a;
  --line:#e3e3e3;
  --light:#f6f6f6;
  --white:#ffffff;
}
*{box-sizing:border-box;margin:0;padding:0}
html,body{width:1200px;height:3550px;overflow:hidden;background:var(--white)}
body{font-family:"Open Sans",Arial,sans-serif;color:var(--text);font-size:12px;line-height:1.9}
h1,h2,h3,h4,.brand{font-family:"Montserrat",Arial,sans-serif;color:var(--ink)}
.section-title{font-size:30px;font-weight:500;text-align:center;letter-spacing:.5px}
.btn{display:inline-block;background:var(--accent);color:var(--white);font-size:11px;font-weight:700;padding:6px 14px;letter-spacing:.3px}

/* hero */
.hero{position:relative;height:556px;background:
  radial-gradient(ellipse at 78% 30%,rgba(70,110,40,.55),transparent 45%),
  radial-gradient(ellipse at 12% 18%,rgba(240,210,120,.55),transparent 22%),
  linear-gradient(150deg,#5a4330 0%,#9c5a3a 30%,#c8704a 48%,#7a4a30 66%,#3c3322 100%)}
.hero::after{content:"";position:absolute;inset:0;background:rgba(0,0,0,.32)}
.hero>*{position:relative;z-index:1}
.topbar{display:flex;justify-content:space-between;align-items:center;padding:28px 97px 0}
.topbar .brand{color:var(--white);font-size:20px;font-weight:600}
.menu-toggle{width:34px;height:34px;border:2px solid var(--white);border-radius:50%;display:flex;flex-direction:column;align-items:center;justify-content:center;gap:3px}
.menu-toggle span{width:12px;height:2px;background:var(--white)}
.hero-title{text-align:center;margin-top:170px;color:var(--white)}
.hero-title .brand{color:var(--white);font-size:58px;font-weight:300;letter-spacing:2px;line-height:1}
.hero-title p{font-family:"Open Sans",sans-serif;font-size:27px;font-weight:600;margin-top:50px;line-height:1.2}
.slider-dots{position:absolute;left:0;right:0;top:497px;display:flex;justify-content:center;gap:7px}
.slider-dots i{width:14px;height:14px;border:2px solid var(--white);border-radius:50%}
.slider-dots i.on{background:var(--accent);border-color:var(--accent)}

/* how it works */
.how{height:870px;padding-top:0}
.how-wrap{position:absolute;top:605px;left:170px;width:860px;text-align:center}
.how-wrap p{font-size:12px;line-height:2.2;margin-top:0}
.how-wrap .section-title{margin-bottom:22px}
.how-wrap p+p{margin-top:22px}
.divider{position:absolute;top:900px;left:97px;width:1006px;height:1px;background:var(--line)}

/* about */
.about-photo{position:absolute;top:959px;left:99px;width:346px;height:409px;border:1px solid var(--line);padding:7px;background:var(--white)}
.about-photo div{width:100%;height:100%;background:linear-gradient(160deg,#b89a78,#6e5a48 45%,#d8d4cf 70%,#8a7a6a)}
.about-text{position:absolute;top:955px;left:504px;width:600px}
.about-text h2{font-size:30px;font-weight:500;margin-bottom:18px}
.about-text p{font-size:12px;line-height:2.45}
.about-text p+p{margin-top:40px}
.about-text .btn{margin-top:22px}

/* services */
.services{position:absolute;top:1425px;left:0;width:1200px;height:409px;background:var(--accent)}
.services .section-title{color:var(--white);position:absolute;top:42px;width:100%}
.service{position:absolute;width:350px;height:138px;padding:20px 16px 0 125px;color:var(--white)}
.service.active{background:var(--white);color:var(--text);box-shadow:0 2px 8px rgba(0,0,0,.12)}
.service h3{font-family:"Montserrat",sans-serif;font-size:19px;font-weight:500;color:inherit;line-height:1.2;margin-bottom:6px}
.service.active h3{color:var(--ink)}
.service p{font-size:12px;line-height:1.85}
.service .icon{position:absolute;left:20px;top:20px;width:90px;height:90px;border-radius:50%;border:2px solid var(--white);display:flex;align-items:center;justify-content:center}
.service.active .icon{border-color:var(--accent)}

/* nutrition */
.nutrition{position:absolute;top:1834px;left:0;width:1200px;height:450px;background:var(--light)}
.nutrition-text{position:absolute;left:97px;top:55px;width:470px}
.nutrition-text h2{font-size:32px;font-weight:500;margin-bottom:18px}
.nutrition-text ul{list-style:none;margin-top:16px}
.nutrition-text li{position:relative;padding-left:26px;margin-bottom:8px}
.nutrition-text li svg{position:absolute;left:0;top:5px}
.nutrition-text .btn{margin-top:12px}
.nutrition-photo{position:absolute;left:600px;top:0;width:600px;height:450px;background:radial-gradient(ellipse at 45% 62%,#6a7a70,transparent 40%),linear-gradient(135deg,#3a2a22,#7a5a44 40%,#2c2a28 75%,#1c1d20)}

/* recipes */
.recipes-title{position:absolute;top:2340px;width:1200px}
.recipe{position:absolute;width:493px;height:197px;border:1px solid #d8d8d8;display:flex;background:var(--white)}
.recipe .photo{width:190px;height:100%}
.recipe .body{padding:14px 16px 0}
.recipe h4{font-size:17px;font-weight:500;margin-bottom:4px}
.recipe ul{list-style:none}
.recipe li{font-size:10.5px;line-height:2.4;padding-left:17px;position:relative;color:#555}
.recipe li svg{position:absolute;left:0;top:8px}
.recipe .more{display:block;font-size:11px;font-weight:700;color:var(--accent);margin-top:5px}
.recipe.featured{border-color:var(--accent)}
.recipe.featured .body{background:var(--accent);flex:1}
.recipe.featured h4,.recipe.featured li,.recipe.featured .more{color:var(--white)}
.explore{position:absolute;top:2888px;left:502px;width:196px;height:42px;border:2px solid #d8d8d8;color:var(--accent);font-size:11px;font-weight:700;text-align:center;line-height:38px}

/* contact */
.contact-rule{position:absolute;top:2985px;left:0;width:1200px;height:5px;background:var(--accent)}
.contact-title{position:absolute;top:3028px;width:1200px}
.contact-form{position:absolute;top:3105px;left:97px;width:632px}
.contact h4{font-size:15px;font-weight:600;margin-bottom:14px}
.field-row{display:flex;gap:10px}
.field{flex:1;margin-bottom:10px}
.field label{display:block;font-size:10.5px;line-height:1.4;margin-bottom:4px;color:#555}
.field .input{height:33px;border:1px solid #cfcfcf}
.field .input.tall{height:83px}
.submit{float:right;background:var(--accent);color:var(--white);font-size:11px;font-weight:700;padding:8px 20px;margin-top:2px}
.contact-info{position:absolute;top:3105px;left:809px;width:300px}
.info-row{display:flex;align-items:center;gap:30px;margin-bottom:18px;font-size:11px;line-height:1.6;color:#555}
.info-row .circle{width:36px;height:36px;border:1px solid var(--accent);border-radius:50%;display:flex;align-items:center;justify-content:center;flex:none}
.hours{margin-top:26px}
.hours table{border-collapse:collapse;font-size:11px;color:#555}
.hours td{padding:3px 0;border-bottom:1px solid var(--line)}
.hours td:first-child{width:150px}

/* footer */
.footer{position:absolute;top:3475px;left:97px;width:1006px;border-top:1px solid var(--line);padding-top:22px;display:flex;justify-content:space-between;align-items:center;font-size:11px}
.social{display:flex;gap:12px}
.social i{width:26px;height:26px;background:#b0b0b0;border-radius:4px}
</style>
</head>
<body>

<header class="hero" role="img" aria-label="Hero photo: grilled salmon fillet with herbs and lemon on a wooden board">
  <div class="topbar">
    <span class="brand">LEO CHEF</span>
    <span class="menu-toggle"><span></span><span></span><span></span></span>
  </div>
  <div class="hero-title">
    <div class="brand">LEO CHEF</div>
    <p>Private Chef in Megayacht and Villas</p>
  </div>
  <div class="slider-dots"><i class="on"></i><i></i><i></i><i></i><i></i></div>
</header>

<section class="how">
  <div class="how-wrap">
    <h2 class="section-title">HOW IT WORKS</h2>
    <p>Our first consultation will be in your home. We will discuss any food preferences you may have, as well as any allergy or dietary needs. At this time we will also discuss what kind of meals you like, from meat and potatoes to all organic, vegan and vegetarian meals or international cuisine like Italian or Mexican. If you have concerns about your diet we can work with any restrictions you have.</p>
    <p>On your scheduled cook date: We will prepare your meals in our commercial kitchen and drop them off to you at your convenience. Your meals will be chilled, packaged, labeled and stored in your refrigerator or freezer with easy instructions for heating. Meals can be packaged in single servings or family style. All meals will have special heating instructions which most only require you heating it up in the oven.</p>
  </div>
  <div class="divider"></div>
</section>

<section class="about">
  <div class="about-photo"><div role="img" aria-label="Portrait of the chef in white jacket standing in a bakery kitchen"></div></div>
  <div class="about-text">
    <h2>LEO CHEF</h2>
    <p>At vero eos et accusamus et iusto odio dignissimos ducimus qui blanditiis praesentium voluptatum deleniti atque corrupti quos dolores et quas molestias excepturi.</p>
    <p>Sint occaecati cupiditate non provident, similique sunt in culpa qui officia deserunt mollitia animi, id est laborum et dolorum fuga. Et harum quidem rerum facilis est et expedita distinctio. Nam libero tempore, cum soluta nobis est eligendi optio cumque nihil impedit quo minus id quod maxime placeat facere possimus omnis voluptas assumenda est, omnis dolor repellendus. Temporibus autem quibusdam et aut officiis debitis aut rerum necessitatibus saepe eveniet ut et voluptates. Et harum quidem rerum facilis est et expedita distinctio. Nam libero tempore, cum eligendi optio cumque nihil impe.</p>
    <span class="btn">READ MORE &gt;&gt;</span>
  </div>
</section>

<section class="services">
  <h2 class="section-title">OUR SERVICES</h2>

  <div class="service active" style="left:83px;top:95px">
    <span class="icon"><svg width="44" height="44" viewBox="0 0 44 44" fill="var(--accent)"><rect x="12" y="4" width="20" height="12" rx="6"/><circle cx="22" cy="22" r="7"/><path d="M8 42c0-9 6-13 14-13s14 4 14 13z"/></svg></span>
    <h3>Private Chef</h3>
    <p>At vero eos et accusamus et iusto odio dignissimos ducimus qui bla nditiis praesentium</p>
  </div>
  <div class="service" style="left:425px;top:95px">
    <span class="icon"><svg width="46" height="40" viewBox="0 0 46 40" fill="#fff"><circle cx="23" cy="10" r="7"/><circle cx="9" cy="15" r="5"/><circle cx="37" cy="15" r="5"/><path d="M11 38c0-9 5-14 12-14s12 5 12 14z"/><path d="M0 36c0-7 4-11 9-11 2 0 3 .5 4 1-2 3-3 6-3 10z"/><path d="M46 36c0-7-4-11-9-11-2 0-3 .5-4 1 2 3 3 6 3 10z"/></svg></span>
    <h3>Personal Chef</h3>
    <p>At vero eos et accusamus et iusto odio dignissimos ducimus qui bla nditiis praesentium</p>
  </div>
  <div class="service" style="left:767px;top:95px">
    <span class="icon"><svg width="46" height="40" viewBox="0 0 46 40" fill="#fff"><path d="M16 36C4 28 1 22 1 16a8 8 0 0 1 15-4 8 8 0 0 1 15 4c0 6-3 12-15 20z"/><path d="M31 38c-7-5-9-8-9-12a5 5 0 0 1 9-3 5 5 0 0 1 9 3c0 4-2 7-9 12z" stroke="var(--accent)" stroke-width="1.5"/></svg></span>
    <h3>Romantic dinner for two</h3>
    <p>At vero eos et accusamus et iusto odio dignissimos ducimus qui bla nditiis praesentium</p>
  </div>

  <div class="service" style="left:83px;top:240px">
    <span class="icon"><svg width="40" height="46" viewBox="0 0 40 46" fill="#fff"><circle cx="20" cy="9" r="7"/><path d="M4 46c0-14 7-20 16-20s16 6 16 20z"/><rect x="16" y="30" width="8" height="11" fill="var(--accent)"/></svg></span>
    <h3>Professional Sommelier</h3>
    <p>At vero eos et accusamus et iusto odio dignissimos ducimus qui bla nditiis praesentium</p>
  </div>
  <div class="service" style="left:425px;top:240px">
    <span class="icon"><svg width="44" height="44" viewBox="0 0 44 44" fill="none" stroke="#fff" stroke-width="4" stroke-linecap="round"><path d="M8 6l28 32"/><path d="M36 6L8 38"/><path d="M30 6l8 8" stroke-width="3"/></svg></span>
    <h3>Build your kitchen</h3>
    <p>At vero eos et accusamus et iusto odio dignissimos ducimus qui bla nditiis praesentium</p>
  </div>
  <div class="service" style="left:767px;top:240px">
    <span class="icon"><svg width="34" height="46" viewBox="0 0 34 46" fill="#fff"><rect x="12" y="0" width="10" height="8"/><path d="M10 8h14l6 10v26H4V18z"/><rect x="9" y="24" width="16" height="10" fill="var(--accent)"/></svg></span>
    <h3>Other Services</h3>
    <p>At vero eos et accusamus et iusto odio dignissimos ducimus qui bla nditiis praesentium</p>
  </div>
</section>

<section class="nutrition">
  <div class="nutrition-text">
    <h2>NUTRITIONAL ADVICES</h2>
    <p>At vero eos et accusamus et iusto odio dignissimos ducimus qui blanditiis praesen tium voluptatum deleniti atque corrupti quos quisquecati.</p>
    <ul>
      <li><svg width="14" height="14" viewBox="0 0 14 14"><circle cx="7" cy="7" r="7" fill="var(--accent)"/><path d="M4 7l2 2 4-4" stroke="#fff" stroke-width="1.6" fill="none"/></svg>Nam libero tempore, cum soluta nobis est eligendi optio ostru</li>
      <li><svg width="14" height="14" viewBox="0 0 14 14"><circle cx="7" cy="7" r="7" fill="var(--accent)"/><path d="M4 7l2 2 4-4" stroke="#fff" stroke-width="1.6" fill="none"/></svg>Debitis aut rerum necessitatibus saepe eveniet ut et voluptat</li>
      <li><svg width="14" height="14" viewBox="0 0 14 14"><circle cx="7" cy="7" r="7" fill="var(--accent)"/><path d="M4 7l2 2 4-4" stroke="#fff" stroke-width="1.6" fill="none"/></svg>Ut aut reiciendis voluptatibus maiores alias consequatur volup</li>
      <li><svg width="14" height="14" viewBox="0 0 14 14"><circle cx="7" cy="7" r="7" fill="var(--accent)"/><path d="M4 7l2 2 4-4" stroke="#fff" stroke-width="1.6" fill="none"/></svg>Ut enim ad minima veniam, quis nostrum exercitationem ulois</li>
    </ul>
    <span class="btn">READ MORE &gt;&gt;</span>
  </div>
  <div class="nutrition-photo" role="img" aria-label="Chef plating a dish with tweezers"></div>
</section>

<section class="recipes">
  <h2 class="section-title recipes-title">MY RECIPES</h2>

  <article class="recipe featured" style="left:97px;top:2419px">
    <div class="photo" role="img" aria-label="Seafood tacos with lime" style="background:linear-gradient(135deg,#d8b070,#b86a3a 50%,#9aa850)"></div>
    <div class="body">
      <h4>SEAFOOD</h4>
      <ul>
        <li><svg width="10" height="8" viewBox="0 0 10 8"><path d="M1 4l3 3 5-6" stroke="#fff" stroke-width="1.8" fill="none"/></svg>Thai Style Mahi with a Coconut Couscous</li>
        <li><svg width="10" height="8" viewBox="0 0 10 8"><path d="M1 4l3 3 5-6" stroke="#fff" stroke-width="1.8" fill="none"/></svg>Garlic and Herb Crusted Seabass</li>
        <li><svg width="10" height="8" viewBox="0 0 10 8"><path d="M1 4l3 3 5-6" stroke="#fff" stroke-width="1.8" fill="none"/></svg>Poached Halibut with Leeks &amp; Grape Tomatoes</li>
        <li><svg width="10" height="8" viewBox="0 0 10 8"><path d="M1 4l3 3 5-6" stroke="#fff" stroke-width="1.8" fill="none"/></svg>Miso Salmon with a Ginger Jasmine Rice</li>
      </ul>
      <span class="more">VIEW MORE &gt;&gt;</span>
    </div>
  </article>

  <article class="recipe" style="left:608px;top:2419px">
    <div class="photo" role="img" aria-label="Sliced roast beef" style="background:linear-gradient(135deg,#3a2a22,#8a3a2a 50%,#5a3a2a)"></div>
    <div class="body">
      <h4>BEEF</h4>
      <ul>
        <li><svg width="10" height="8" viewBox="0 0 10 8"><path d="M1 4l3 3 5-6" stroke="var(--accent)" stroke-width="1.8" fill="none"/></svg>Grilled Teriyaki Steak Tips</li>
        <li><svg width="10" height="8" viewBox="0 0 10 8"><path d="M1 4l3 3 5-6" stroke="var(--accent)" stroke-width="1.8" fill="none"/></svg>Slow Cooked Smokey Chipotle Tacos</li>
        <li><svg width="10" height="8" viewBox="0 0 10 8"><path d="M1 4l3 3 5-6" stroke="var(--accent)" stroke-width="1.8" fill="none"/></svg>Beef Tenderloin in a Mushroom Brandy Sauce</li>
        <li><svg width="10" height="8" viewBox="0 0 10 8"><path d="M1 4l3 3 5-6" stroke="var(--accent)" stroke-width="1.8" fill="none"/></svg>Penne Bolognese or Classic Meat Lasagna</li>
      </ul>
      <span class="more">VIEW MORE &gt;&gt;</span>
    </div>
  </article>

  <article class="recipe" style="left:97px;top:2639px">
    <div class="photo" role="img" aria-label="Chicken with herbs and vegetables" style="background:linear-gradient(135deg,#c8b890,#8a8040 50%,#d0c8b0)"></div>
    <div class="body">
      <h4>CHICKEN</h4>
      <ul>
        <li><svg width="10" height="8" viewBox="0 0 10 8"><path d="M1 4l3 3 5-6" stroke="var(--accent)" stroke-width="1.8" fill="none"/></svg>Chicken with Arugula with a Basil Pasta Salad</li>
        <li><svg width="10" height="8" viewBox="0 0 10 8"><path d="M1 4l3 3 5-6" stroke="var(--accent)" stroke-width="1.8" fill="none"/></svg>Baked Chicken with Sweet Potato and Radish</li>
        <li><svg width="10" height="8" viewBox="0 0 10 8"><path d="M1 4l3 3 5-6" stroke="var(--accent)" stroke-width="1.8" fill="none"/></svg>Marsala, Mushrooms, Pancetta, Marsala wine</li>
        <li><svg width="10" height="8" viewBox="0 0 10 8"><path d="M1 4l3 3 5-6" stroke="var(--accent)" stroke-width="1.8" fill="none"/></svg>Curry Spiced Chicken Bread with a Yogurt</li>
      </ul>
      <span class="more">VIEW MORE &gt;&gt;</span>
    </div>
  </article>

  <article class="recipe" style="left:608px;top:2639px">
    <div class="photo" role="img" aria-label="Grilled pork chop on a plate" style="background:linear-gradient(135deg,#e8e0d8,#9a5a30 45%,#c8c0b8)"></div>
    <div class="body">
      <h4>PORK</h4>
      <ul>
        <li><svg width="10" height="8" viewBox="0 0 10 8"><path d="M1 4l3 3 5-6" stroke="var(--accent)" stroke-width="1.8" fill="none"/></svg>Oriental Sweet and Sour Pork</li>
        <li><svg width="10" height="8" viewBox="0 0 10 8"><path d="M1 4l3 3 5-6" stroke="var(--accent)" stroke-width="1.8" fill="none"/></svg>Maple Dijon Glazed Pork Medallions</li>
        <li><svg width="10" height="8" viewBox="0 0 10 8"><path d="M1 4l3 3 5-6" stroke="var(--accent)" stroke-width="1.8" fill="none"/></svg>Crispy Corn Flake Pan Fried Pork Chops</li>
        <li><svg width="10" height="8" viewBox="0 0 10 8"><path d="M1 4l3 3 5-6" stroke="var(--accent)" stroke-width="1.8" fill="none"/></svg>Creamy Pork Chops with Mushrooms, Haricot</li>
      </ul>
      <span class="more">VIEW MORE &gt;&gt;</span>
    </div>
  </article>

  <span class="explore">EXPLORE MORE &gt;&gt;</span>
</section>

<section class="contact">
  <div class="contact-rule"></div>
  <h2 class="section-title contact-title">CONTACT US</h2>

  <div class="contact-form">
    <h4>CONTACT FORM</h4>
    <div class="field-row">
      <div class="field"><label>NAME :</label><div class="input"></div></div>
      <div class="field"><label>PHONE NO :</label><div class="input"></div></div>
    </div>
    <div class="field"><label>EMAIL :</label><div class="input"></div></div>
    <div class="field"><label>MESSAGE :</label><div class="input tall"></div></div>
    <span class="submit">SUBMIT</span>
  </div>

  <div class="contact-info">
    <h4>CONTACT INFORMATION</h4>
    <div class="info-row">
      <span class="circle"><svg width="14" height="18" viewBox="0 0 14 18"><path d="M7 0a7 7 0 0 1 7 7c0 5-7 11-7 11S0 12 0 7a7 7 0 0 1 7-7z" fill="var(--accent)"/><circle cx="7" cy="7" r="2.5" fill="#fff"/></svg></span>
      <span>Street # 210 - 36<br>Harbor Town 40210</span>
    </div>
    <div class="info-row">
      <span class="circle"><svg width="18" height="13" viewBox="0 0 18 13"><rect width="18" height="13" rx="1.5" fill="var(--accent)"/><path d="M1 1.5l8 6 8-6" stroke="#fff" stroke-width="1.4" fill="none"/></svg></span>
      <span>info@leochef.com</span>
    </div>
    <div class="info-row">
      <span class="circle"><svg width="16" height="16" viewBox="0 0 16 16"><path d="M3 0l3 4-2 2c1 2.5 3.5 5 6 6l2-2 4 3-2 3C7 16 0 9 0 2z" fill="var(--accent)"/></svg></span>
      <span>1 - 555 - 010 - 2040</span>
    </div>
    <div class="hours">
      <h4>OPENING HOURS</h4>
      <table>
        <tr><td>Monday - Wednesday</td><td>10:00 am - 10:00 pm</td></tr>
        <tr><td>Thursday &amp; Friday</td><td>10:00 am - 10:00 pm</td></tr>
        <tr><td>Saturday &amp; Sunday</td><td>9:00 am - 11:00 pm</td></tr>
      </table>
    </div>
  </div>

  <footer class="footer">
    <span>Copyrights © 2016, Leo Chef . All Rights Reserved.</span>
    <span class="social" aria-label="Social links"><i></i><i></i><i></i><i></i></span>
  </footer>
</section>

</body>
</html>
```